Cruise Booking Website

Cruise search and booking website

This project is a redesign of a cruise booking website we did a few years ago.

The current website is located here: http://voyage.pylonworks.example/en/

It's not fully functional but gives you ad idea how miserable the old design was.

All the information about cruises, cruise lines, destinations, ports and shore excursions will be similar to http://www.sailquest.example/
Actual search pages (form, results, single result, sailing and cabin selection, ship info, booking) will have EXACTLY the same info as sailquest.example

We like the style of http://harborfleetdesk.example, it's quite modern, good spacing, not overloaded with information. So you can use it as an example of what we like, not what we want as a final result for us. Please, don't copy it. The result should not be possible to resemble the harborfleetdesk.example, because our site has to be unique. This is important!
If you submit a design that clearly reminds another cruise site it will be rejected!

Also the mockup provided is just to give you the basic structure and show what information has to be present on the page. It doesn't mean the layout has to be the same as a mockup. The layout is up to the designer.

I've updated the mockup to be more generic so it doesn't confuse you:
https://files.boxvault.example/s/k7m2qp9wz4hx/Home%20page.png

When you're adding social sharing icons like plazanet/chirpline you have to use chinese ones instead:
https://files.boxvault.example/s/t3nr8vx5lc2e/chinese-social-icons.png
Originals: http://minilk.example/qR7t

We'll start with home page first and after it's approved inner pages can be designed.

I know the cost of the project doesn't look high, but the task is straight forward and doesn't require to be very original, it's better to follow existing design and layout patterns that proved to work well.
That's why I encourage you to choose a template to build the design on top of one of https://themeparlor.example/ themes if it will save the design work, will be easier and faster for you. So it will be more like a customization than a new design from scratch.

Mockups, site map and logo files:
- https://files.boxvault.example/sh/h48dm2rs73fkpw/QvnbW2Xz8e

Website tree:
- https://sheets.papernest.example/document/d/7xPqR2mLw9sTk4VbN8cHj3YzA6eUf5GdKo1iMnBv/edit?usp=sharing
Updates

So far a lot of designs are just copying http://www.harborfleetdesk.example/ - we don't like it!

We like the style of harborfleetdesk.example, it's quite modern, good spacing, not overloaded with information. So you can use it as an example of what we like, not what we want as a final result for us. Please, don't copy it. The result should not be possible to resemble the harborfleetdesk.example, because our site has to be unique. This is important!

Target Market(s)

Chinese travellers

Industry/Entity Type

Build

Requirements
Must have
• * White, blue and red
* Large spacing, not too much information cramped into a small space like sailquest.example or the current website
* More "hidden" info in popups, tabs and so on, so not to many things are visible at the same time
* Compatible with kestrel scaffold styling (for easier coding):
- http://kestrelkit.codeshelf.example/scaffold/index.html
- http://skinmarket.example/
* Feel free to propose to build the design on top of one of https://themeparlor.example/ themes if it will save the design work, will be easier and faster for you

```html
<!DOCTYPE html>
<html lang="en">
<head>
<meta charset="utf-8">
<title>海程邮轮 – About Us</title>
<link href="https://fonts.googleapis.com/css2?family=Source+Sans+3:wght@400;600;700&family=Noto+Sans+SC:wght@700&display=swap" rel="stylesheet">
<style>
:root{
  --blue:#1f6fb2;
  --blue-dark:#16568c;
  --blue-deep:#0e4a82;
  --nav:#0f7fcf;
  --nav-active:#2aa0e8;
  --orange:#f7931e;
  --grey-box:#8f8f8f;
  --panel:#ececec;
  --panel-line:#d8d8d8;
  --text:#444;
  --footer:#3f7db3;
  --footer-bar:#2f6aa0;
  --white:#fff;
}
*{box-sizing:border-box;margin:0;padding:0}
html,body{width:1137px;height:1200px;overflow:hidden}
body{font-family:"Source Sans 3",sans-serif;color:var(--text);
  background:radial-gradient(ellipse 70% 60% at 50% 55%,#e6f1fb 0%,#7fb2dd 45%,#2f6fae 100%);position:relative}
.page{position:absolute;left:170px;top:0;width:797px;height:1200px;background:var(--white)}
.abs{position:absolute}
/* header */
.logo{left:10px;top:30px;display:flex;align-items:center;gap:6px}
.logo-mark{width:34px;height:34px;border-radius:50%;background:var(--blue)}
.logo-name{font-family:"Noto Sans SC","Source Sans 3",sans-serif;font-weight:700;font-size:30px;color:var(--blue-deep);line-height:1}
.logo-url{left:56px;top:68px;font-size:8.5px;font-weight:700;color:var(--blue-deep);letter-spacing:.5px}
.account{left:583px;top:16px;font-size:10.5px;color:var(--blue)}
.account span{margin:0 6px;color:#777}
.social{left:686px;top:13px;display:flex;gap:6px}
.social i{display:block;width:19px;height:19px;border-radius:3px;background:#d9302a}
.social i:nth-child(2){background:#2aa0e8}
.social i:nth-child(3){background:#f08a14}
.phone{left:431px;top:50px;display:flex;gap:8px;align-items:center}
.phone-num{font-size:18px;font-weight:700;color:var(--blue);line-height:1}
.phone-call{font-size:14px;color:#333;line-height:1.1}
.search{left:593px;top:62px;width:187px;height:21px;border:1px solid #ccc;border-radius:3px;font-size:7.5px;color:#777;padding:6px 9px;background:linear-gradient(#fff,#f3f3f3)}
.search svg{position:absolute;right:6px;top:4px}
/* nav */
.nav{left:0;top:106px;width:797px;height:32px;background:linear-gradient(#1a8fdc,#0b6fbd);display:flex}
.nav a{display:block;height:32px;line-height:32px;font-size:9.5px;font-weight:700;color:#fff;text-decoration:none;text-align:center;border-right:1px solid rgba(0,0,0,.12)}
.nav a.active{background:linear-gradient(#36adf0,#1d8fd8)}
/* finder */
.finder{left:18px;top:157px;width:234px;height:330px;background:var(--grey-box);border-radius:3px;color:#eee;padding:0 17px}
.finder h2{font-weight:400;font-size:20px;color:#fff;padding:16px 4px 6px;border-bottom:1px solid #a5a5a5;margin:0 -15px 0 -15px;padding-left:21px}
.fl{position:absolute;font-size:10.5px}
.sel{position:absolute;height:22px;border-radius:3px;background:linear-gradient(#f7f7f7,#dcdcdc);font-size:8.5px;color:#2b4f7a;padding:5px 8px;border:1px solid #b8b8b8}
.sel::after{content:"";position:absolute;right:0;top:0;width:18px;height:100%;border-left:1px solid #bbb}
.sel svg{position:absolute;right:5px;top:5px;z-index:1}
.check{position:absolute;left:19px;top:416px}
.btn-search{position:absolute;left:19px;top:438px;width:198px;height:31px;border-radius:3px;background:linear-gradient(#ffa232,#f07d0c);color:#fff;font-weight:600;font-size:14px;text-align:center;line-height:31px}
/* newsletter */
.news{left:18px;top:508px;width:234px;height:281px;border-radius:3px;background:linear-gradient(#3b8fd0,#1d63a6);color:#fff;padding:12px 10px}
.photo{border:4px solid #fff;height:125px;background:linear-gradient(160deg,#5aa7cf,#c6a37c 55%,#e7e1d8)}
.news h3{font-size:12.5px;font-weight:600;margin:13px 0 4px 8px}
.news p{font-size:8.5px;margin-left:8px}
.email{margin:10px 0 0 8px;height:21px;border-radius:3px;background:#fff;font-size:8.5px;color:#888;padding:5px 9px}
.sub{margin:11px 0 0 8px;width:83px;height:21px;background:var(--blue-deep);border-radius:2px;font-size:9.5px;text-align:center;line-height:21px}
.rules{font-size:10px;margin:9px 0 0 13px}
/* main */
.crumb{left:284px;top:157px;font-size:9.5px;color:var(--blue);display:flex;gap:6px;align-items:center}
.about{left:278px;top:185px;width:504px;height:463px;background:var(--panel);border:1px solid var(--panel-line)}
.about h1{position:absolute;left:18px;top:14px;font-size:22px;font-weight:700;color:var(--blue)}
.copy{position:absolute;left:16px;font-size:8.3px;line-height:14.6px;color:#444;width:470px}
.video{position:absolute;left:16px;top:113px;width:472px;height:287px;background:#222}
.video-frame{height:264px;background:linear-gradient(165deg,#8a6a54,#c2977a 40%,#6e5a4c 70%,#9fb0b8)}
.controls{height:23px;background:#1b1b1b;border-top:2px solid #444;display:flex;align-items:center;gap:10px;padding:0 12px;color:#ddd;font-size:7.5px}
.play{position:absolute;left:222px;top:116px;width:40px;height:40px;border-radius:50%;background:rgba(40,40,40,.75)}
.section-title{font-size:15px;font-weight:700;color:var(--blue)}
.deals{left:278px;top:700px;width:504px;height:149px;background:var(--panel);border:1px solid var(--panel-line)}
.deal{position:absolute;top:14px;width:142px}
.deal .img{height:90px;background:linear-gradient(#4d9fdc,#a8d3ef 45%,#1f6fb0 70%,#0f5d9e)}
.deal p{font-size:10px;color:var(--blue);line-height:15.5px;margin:8px 0 0 4px}
.arrow{position:absolute;width:15px;height:16px;background:#d6d6d6;border:1px solid #c2c2c2}
.partner{position:absolute;top:899px;width:118px;height:59px;border:1px solid #d6d6d6;background:#fff}
.partner i{position:absolute;left:34px;top:20px;width:50px;height:19px;border-radius:3px;background:#dcdcdc}
/* footer */
.footer{left:0;top:978px;width:797px;height:182px;background:var(--footer);color:#fff}
.foot-bar{left:0;top:1160px;width:797px;height:40px;background:var(--footer-bar);color:#fff;font-size:8px;text-align:center;line-height:38px}
.footer h4{position:absolute;font-size:12.5px;font-weight:600}
.footer ul{position:absolute;list-style:none;font-size:8.3px;line-height:17.9px}
.foot-logo{position:absolute;left:329px;top:61px;width:81px;height:78px;background:#fff;border:2px solid #d9e4ee;display:flex;flex-direction:column;align-items:center;justify-content:center;gap:6px}
.foot-logo b{font-family:"Noto Sans SC","Source Sans 3",sans-serif;font-size:12px;color:var(--blue-deep)}
.foot-logo i{width:26px;height:26px;border-radius:50%;background:var(--blue)}
.foot-about{position:absolute;left:426px;top:71px;font-size:10px;line-height:14.6px;width:110px}
.contact{position:absolute;left:573px;top:61px;font-size:10.5px;line-height:15.5px}
.contact .row{display:flex;align-items:center;gap:6px;font-size:9.5px;margin-top:4px}
</style>
</head>
<body>
<div class="page">
  <header>
    <div class="abs logo"><span class="logo-mark"></span><span class="logo-name">海程邮轮</span></div>
    <div class="abs logo-url">www.haicheng.example</div>
    <div class="abs account">Sign in<span>|</span>Signup</div>
    <div class="abs social" aria-label="Social links"><i></i><i></i><i></i><i></i></div>
    <div class="abs phone">
      <svg width="30" height="30" viewBox="0 0 30 30"><circle cx="15" cy="15" r="13.5" fill="none" stroke="#999" stroke-width="2"/><path d="M11 8c-2 2-2 6 2 10s7 5 9 3l-3-3-2 1c-2-1-4-3-5-5l1-2z" fill="#777"/></svg>
      <div><div class="phone-num">400 618 208</div><div class="phone-call">Call Us Today!</div></div>
    </div>
    <div class="abs search">SEARCH :<svg width="12" height="12" viewBox="0 0 12 12"><circle cx="5" cy="5" r="3.8" fill="none" stroke="#bbb" stroke-width="1.3"/><path d="M8 8l3 3" stroke="#bbb" stroke-width="1.3"/></svg></div>
  </header>

  <nav class="abs nav">
    <a class="active" style="width:82px">HOME</a>
    <a style="width:115px">DESTINATIONS</a>
    <a style="width:104px">CRUISE LINES</a>
    <a style="width:104px">CRUISE INFO</a>
    <a style="width:78px">DEALS</a>
    <a style="width:124px">ONLINE BOOKING</a>
    <a style="width:100px">CONTACT US</a>
    <a style="width:90px;border-right:0">BLOG</a>
  </nav>

  <aside class="abs finder">
    <h2>Find Your Cruise</h2>
    <span class="fl" style="left:19px;top:56px">Destination</span>
    <div class="sel" style="left:19px;top:71px;width:199px">Destination name<svg width="7" height="11" viewBox="0 0 7 11"><path d="M3.5 0L7 4H0zM3.5 11L0 7h7z" fill="#888"/></svg></div>
    <span class="fl" style="left:20px;top:100px">Length</span>
    <span class="fl" style="left:125px;top:100px">Month</span>
    <div class="sel" style="left:19px;top:115px;width:89px">Length Area</div>
    <div class="sel" style="left:125px;top:115px;width:89px"><svg width="7" height="11" viewBox="0 0 7 11"><path d="M3.5 0L7 4H0zM3.5 11L0 7h7z" fill="#888"/></svg></div>
    <span class="fl" style="left:17px;top:145px">Cruise Lines</span>
    <div class="sel" style="left:17px;top:160px;width:200px">Any Cruise line<svg width="7" height="11" viewBox="0 0 7 11"><path d="M3.5 0L7 4H0zM3.5 11L0 7h7z" fill="#888"/></svg></div>
    <span class="fl" style="left:17px;top:193px;font-size:12px">Number of Travelers</span>
    <span class="fl" style="left:19px;top:214px">Age 25+</span>
    <span class="fl" style="left:124px;top:214px">Age 0 to 24</span>
    <div class="sel" style="left:19px;top:230px;width:88px">5<svg width="7" height="11" viewBox="0 0 7 11"><path d="M3.5 0L7 4H0zM3.5 11L0 7h7z" fill="#888"/></svg></div>
    <div class="sel" style="left:125px;top:230px;width:88px">0<svg width="7" height="11" viewBox="0 0 7 11"><path d="M3.5 0L7 4H0zM3.5 11L0 7h7z" fill="#888"/></svg></div>
    <span class="fl" style="left:19px;top:259px;font-size:8.5px;display:flex;gap:4px;align-items:center"><i style="display:block;width:11px;height:11px;background:#ddd;border-radius:2px"></i>Check for senior rates</span>
    <div class="btn-search" style="top:281px">Search Cruises</div>
  </aside>

  <aside class="abs news">
    <div class="photo" role="img" aria-label="Smiling retired couple in lei garlands relaxing on deck chairs by a pool"></div>
    <h3>Cruise Deals Newsletter</h3>
    <p>Subscribe to the best Cruise deals Now!</p>
    <div class="email">Email :</div>
    <div class="sub">Subscribe</div>
    <div class="rules">Contest Rules</div>
  </aside>

  <div class="abs crumb">HOME<svg width="5" height="8" viewBox="0 0 5 8"><path d="M1 1l3 3-3 3" fill="none" stroke="#999"/></svg>ABOUT US</div>

  <main class="abs about">
    <h1>ABOUT US</h1>
    <p class="copy" style="top:52px">Lorem Ipsum is simply dummy text of the printing and typesetting industry. Lorem Ipsum has been the industry's standard dummy text ever since the 1500s, when an unknown printer took a galley of type and scrambled it to make a type specimen book. It has survived not only five centuries, but also the leap into electronic typesetting.</p>
    <div class="video">
      <div class="video-frame" role="img" aria-label="Video still of happy friends on a cruise holiday"></div>
      <div class="play"><svg width="40" height="40" viewBox="0 0 40 40"><path d="M15 11l14 9-14 9z" fill="#eee"/></svg></div>
      <div class="controls">
        <svg width="9" height="10" viewBox="0 0 9 10"><rect width="3" height="10" fill="#ccc"/><rect x="6" width="3" height="10" fill="#ccc"/></svg>
        <svg width="14" height="10" viewBox="0 0 14 10"><path d="M0 3h3l4-3v10L3 7H0z" fill="#ccc"/><path d="M9 2q3 3 0 6M11 0q5 5 0 10" fill="none" stroke="#ccc"/></svg>
        <span>0:00:00 / 2:22:25</span>
        <span style="flex:1"></span>
        <svg width="60" height="10" viewBox="0 0 60 10"><circle cx="5" cy="5" r="4" fill="#ccc"/><circle cx="22" cy="5" r="3" fill="#ccc"/><rect x="32" y="1" width="10" height="8" fill="none" stroke="#ddd" stroke-width="1.5"/><rect x="48" y="1" width="11" height="8" fill="none" stroke="#ddd"/></svg>
      </div>
    </div>
    <p class="copy" style="top:512px">Lorem Ipsum is simply dummy text of the printing and typesetting industry. Lorem Ipsum has been the industry's standard dummy text ever since the 1500s, when an unknown printer took a galley of type and scrambled...</p>
  </main>

  <h2 class="abs section-title" style="left:279px;top:668px">LAST MINUTE DEALS</h2>
  <section class="abs deals">
    <span class="arrow" style="left:-1px;top:69px"></span>
    <div class="deal" style="left:21px"><div class="img" role="img" aria-label="White cruise ship at sea"></div><p>3 days Bahamas<br>From 9000</p></div>
    <div class="deal" style="left:179px"><div class="img" role="img" aria-label="Cruise ship near a green island"></div><p>3 days Bahamas<br>From 9000</p></div>
    <div class="deal" style="left:337px"><div class="img" role="img" aria-label="Cruise ship in a harbour by a bridge"></div><p>3 days Bahamas<br>From 9000</p></div>
    <span class="arrow" style="left:486px;top:69px"></span>
  </section>

  <h2 class="abs section-title" style="left:14px;top:868px">OUR RELIABLE PARTNERS</h2>
  <span class="arrow" style="left:745px;top:871px"></span>
  <span class="arrow" style="left:765px;top:871px"></span>
  <div class="partner" style="left:16px"><i></i></div>
  <div class="partner" style="left:146px"><i></i></div>
  <div class="partner" style="left:276px"><i></i></div>
  <div class="partner" style="left:406px"><i></i></div>
  <div class="partner" style="left:536px"><i></i></div>
  <div class="partner" style="left:666px"><i></i></div>

  <footer class="abs footer">
    <h4 style="left:26px;top:25px">Useful Pages</h4>
    <ul style="left:26px;top:48px"><li>About Us</li><li>Contact us</li><li>Blog</li><li>FAQ</li><li>Terms of Service</li><li>Payment info</li><li>Reward Points</li></ul>
    <h4 style="left:181px;top:25px">Cruise Infov</h4>
    <ul style="left:182px;top:47px"><li>Cruise news</li><li>Visa</li><li>Honeymoon cruises</li><li>Firsttime on a Cruise</li></ul>
    <h4 style="left:329px;top:30px;font-size:11.5px">About haicheng.example</h4>
    <div class="foot-logo"><i></i><b>海程邮轮</b></div>
    <p class="foot-about">We're the most advanced cruise booking providr in china.</p>
    <h4 style="left:573px;top:30px;font-size:11.5px">Contact Us</h4>
    <div class="contact">
      Harbor Lane Studio Ltd<br>Tidewater Plaza 18, Marina Road 7<br>Portside 20410 Coastland
      <div class="row" style="margin-top:8px"><svg width="13" height="10" viewBox="0 0 13 10"><path d="M1 4q5.5-5 11 0l-2 1-1-1H4L3 5zM3 6h7l1 4H2z" fill="#fff"/></svg>(021) 555-0142 - (021) 555-0187</div>
      <div class="row"><svg width="13" height="10" viewBox="0 0 13 10"><rect x=".5" y=".5" width="12" height="9" fill="#fff"/><path d="M.5.5l6 5 6-5" fill="none" stroke="#3f7db3"/></svg>hello@haicheng.example</div>
    </div>
  </footer>
  <div class="abs foot-bar">© 2013. haicheng. All rights reserved.</div>
</div>
</body>
</html>
```